New business card for a regional office of a US M&A company

We need business card for a finance company, office based in Hong Kong , our Head office is in US, our business is to Merge and acquires companies , the new office will be a regional office for the Asia Pacific region. We want to use the head office logo as attached ( but don't have to be exactly the same, can be a variation to it) as a base and then add Asia Pacific alongside the logo.
We would prefer to have be bilingual Eng + Chinese, although we don't really have Chinese company name .

Industry/Entity Type

Business

Contact Information for Business Card

Clara Jo Tsang
 

VP,
APAC M&A Operations
Orin Vantage Asia Pacific Limited
 
Unit 1407, K18
18 Tai Lok Shan Road, 
Hong Kong 
 
M: +852 6038 1742
T : +852 2836 4100
F : +852 2836 4177
VOIP: 4158
 
cjtsang@orinvantage.com

Font styles to use
Serif
Sans Serif

Colors

Designer to choose colors to be used in the design.

Requirements
Must have
• APAC Office

```html
<!DOCTYPE html>
<html lang="en">
<head>
<meta charset="utf-8">
<title>Orin Vantage APAC Business Card</title>
<link rel="stylesheet" href="https://fonts.googleapis.com/css2?family=Open+Sans:wght@800&family=Roboto:wght@400&family=Roboto+Condensed:wght@500&display=swap">
<style>
  :root {
    --backdrop: #232323;
    --navy: #0f2841;
    --cyan: #1eaad0;
    --white: #f2f4f6;
    --muted: #dfe4ea;
  }
  * { margin: 0; padding: 0; box-sizing: border-box; }
  html, body { width: 1200px; height: 960px; overflow: hidden; }
  body {
    background: var(--backdrop);
    position: relative;
    font-family: "Roboto", Arial, sans-serif;
  }
  .card {
    position: absolute;
    left: 320px;
    width: 600px;
    background: var(--navy);
    overflow: hidden;
  }
  .card--front { top: 108px; height: 332px; }
  .card--back { top: 493px; height: 342px; }

  .brand-name {
    position: absolute;
    left: 0; right: 0;
    top: 182px;
    text-align: center;
    font-family: "Open Sans", Arial, sans-serif;
    font-weight: 800;
    font-size: 46px;
    letter-spacing: 0.5px;
    color: var(--cyan);
  }
  .website {
    position: absolute;
    left: 0; right: 0;
    top: 284px;
    text-align: center;
    font-size: 14px;
    letter-spacing: 6.2px;
    color: var(--muted);
  }

  .accent-panel { position: absolute; inset: 0; }
  .accent-name {
    position: absolute;
    left: 330px;
    width: 240px;
    top: 157px;
    text-align: center;
    font-family: "Open Sans", Arial, sans-serif;
    font-weight: 800;
    font-size: 24px;
    color: var(--cyan);
  }

  .person { position: absolute; left: 35px; top: 24px; }
  .person__name {
    font-family: "Roboto Condensed", Arial, sans-serif;
    font-weight: 500;
    font-size: 21px;
    color: var(--cyan);
    text-transform: uppercase;
  }
  .person__title { font-size: 14px; color: var(--white); margin: 2px 0 0 2px; }

  .address {
    position: absolute;
    left: 35px;
    top: 125px;
    font-size: 14px;
    line-height: 19px;
    color: var(--muted);
    list-style: none;
  }
  .phones {
    position: absolute;
    left: 35px;
    top: 225px;
    list-style: none;
    font-size: 14px;
    line-height: 19px;
    color: var(--muted);
  }
  .phones li { display: flex; align-items: center; gap: 8px; }
  .phones svg { width: 15px; height: 14px; fill: var(--cyan); }
  .voip {
    position: absolute;
    left: 35px;
    top: 292px;
    font-size: 14px;
    color: var(--muted);
  }
</style>
</head>
<body>
  <section class="card card--front">
    <p class="brand-name">ORIN VANTAGE</p>
    <p class="website">www.orinvantage.com</p>
  </section>

  <section class="card card--back">
    <svg class="accent-panel" width="600" height="342" viewBox="0 0 600 342" aria-hidden="true">
      <polygon points="430,0 600,0 600,342 430,342 598,171" fill="var(--cyan)"/>
    </svg>
    <p class="accent-name">ORIN VANTAGE</p>

    <div class="person">
      <h1 class="person__name">Clara Jo Tsang</h1>
      <p class="person__title">VP</p>
    </div>

    <ul class="address">
      <li>APAC M&amp;A Operations</li>
      <li>Orin Vantage Asia Pacific Limited</li>
      <li>Unit 1407, K18</li>
      <li>18 Tai Lok Shan Road</li>
      <li>Hong Kong</li>
    </ul>

    <ul class="phones">
      <li>
        <svg viewBox="0 0 24 24" aria-label="Telephone"><path d="M6.6 10.8a15.1 15.1 0 0 0 6.6 6.6l2.2-2.2c.3-.3.7-.4 1-.2 1.1.4 2.3.6 3.6.6.6 0 1 .4 1 1V20c0 .6-.4 1-1 1A17 17 0 0 1 3 4c0-.6.4-1 1-1h3.5c.6 0 1 .4 1 1 0 1.3.2 2.5.6 3.6.1.3 0 .7-.2 1z"/></svg>
        +852 2836 4100
      </li>
      <li>
        <svg viewBox="0 0 24 24" aria-label="Mobile"><path d="M7 1h10a2 2 0 0 1 2 2v18a2 2 0 0 1-2 2H7a2 2 0 0 1-2-2V3a2 2 0 0 1 2-2zm0 3v14h10V4zm5 15.2a1.2 1.2 0 1 0 0 2.4 1.2 1.2 0 0 0 0-2.4z"/></svg>
        +852 6038 1742
      </li>
      <li>
        <svg viewBox="0 0 24 24" aria-label="Fax"><path d="M6 2h12v5H6zM3 8h18a2 2 0 0 1 2 2v8h-4v4H5v-4H1v-8a2 2 0 0 1 2-2zm4 8v4h10v-4zm11-5a1 1 0 1 0 0 2 1 1 0 0 0 0-2z"/></svg>
        +852 2836 4177
      </li>
    </ul>

    <p class="voip">VOIP: 4158</p>
  </section>
</body>
</html>
```